Brochure and Business Card design

I am looking for a high end, elegant A4, 4 page brochure booklet to convey our products to clientele that will be visiting a luxury display showroom.

Harrowgate Locks and Grilles is a Australian security provider, and we supply high end products from reputable brands.
The brochure will be directed to clients building a new home with a partnered building company and will be accompanied with display boards of our products.

I am providing files of a document we have put together with the relevant information and some images to help along the way, we are not bound by the layout or style it has been drawn up and we wish to give you complete creative freedom putting the peaces together. I have also provided the files for our logo in two different colours, and a picture of a brochure we love the look of.

If you have any suggestions, we can likely come up with further images etc if it will help or even if you feel some should be removed, we are open to that also

Target Market(s)

Young familys, people building new luxury homes, proffesionals, home owners

Industry/Entity Type

Business

Font styles to use
Serif
Sans Serif

Requirements
Must have
• All 8 pages
Should not have
• Not really a fan of reds and similar.

```html
<!DOCTYPE html>
<html lang="en">
<head>
<meta charset="utf-8">
<title>Ducted Vacuum – Brochure Spread</title>
<link href="https://fonts.googleapis.com/css2?family=Didact+Gothic&family=Open+Sans:wght@400;700&display=swap" rel="stylesheet">
<style>
  :root {
    --stage: #cfcfcf;
    --paper: #fafafa;
    --green: #8fc043;
    --heading-green: #7cb236;
    --body-grey: #5a5a5a;
    --white: #ffffff;
    --label: #1a1a1a;
  }
  * { margin: 0; padding: 0; box-sizing: border-box; }
  html, body { width: 1200px; height: 645px; overflow: hidden; }
  body {
    position: relative;
    background: var(--stage);
    font-family: "Didact Gothic", "Century Gothic", sans-serif;
  }
  .page-label {
    position: absolute; top: 97px;
    font-family: "Open Sans", sans-serif; font-weight: 700;
    font-size: 12px; color: var(--label);
  }
  .page-label--left { left: 328px; }
  .page-label--right { left: 856px; }

  .page { position: absolute; top: 127px; height: 387px; }
  .page--left { left: 98px; width: 500px; background: var(--white); }
  .page--right { left: 598px; width: 502px; background: var(--paper); }

  .hero-photo {
    position: absolute; left: 0; top: 0; width: 500px; height: 168px;
    background: linear-gradient(90deg, #cfd6dc 0%, #e9e4de 40%, #f1e6da 70%, #dad7d2 100%);
  }
  .feature-band {
    position: absolute; left: 0; top: 173px; width: 500px; height: 214px;
    background: var(--green);
  }
  .accessory-photo {
    position: absolute; left: 22px; top: 28px; width: 148px; height: 160px;
    background: radial-gradient(ellipse at 50% 50%, #8a8f92 0%, #4d5256 55%, rgba(77,82,86,0) 78%);
  }
  .feature-title {
    position: absolute; left: 202px; top: 42px;
    font-weight: 400; font-size: 27px; color: var(--white); letter-spacing: 0.2px;
  }
  .feature-copy {
    position: absolute; left: 202px; top: 92px; width: 240px;
    font-size: 6.6px; line-height: 10.8px; color: rgba(255,255,255,0.92);
  }
  .feature-copy p + p { margin-top: 10.8px; }

  .product-photo {
    position: absolute; left: 34px; top: 37px; width: 112px; height: 232px;
    border-radius: 10px 10px 14px 14px;
    background: linear-gradient(90deg, #3c4550 0%, #5b6672 45%, #46505b 100%);
  }
  .column { position: absolute; top: 44px; width: 128px; }
  .column--one { left: 180px; }
  .column--two { left: 331px; }
  .section-heading {
    font-family: "Open Sans", sans-serif; font-weight: 700;
    font-size: 8.4px; line-height: 9.6px; color: var(--heading-green);
    margin-bottom: 4px;
  }
  .section-body {
    font-size: 5.9px; line-height: 7.4px; color: var(--body-grey);
  }
  .section-body p + p { margin-top: 7px; }
  .section-body strong { font-family: "Open Sans", sans-serif; font-weight: 700; font-size: 5.6px; }
  .section + .section { margin-top: 16px; }
  .column--two .section + .section { margin-top: 34px; }
</style>
</head>
<body>
  <div class="page-label page-label--left">Page 6</div>
  <div class="page-label page-label--right">Page 7</div>

  <section class="page page--left">
    <div class="hero-photo" role="img" aria-label="Photo of a smiling family of a father, mother and two children at home"></div>
    <div class="feature-band">
      <div class="accessory-photo" role="img" aria-label="Photo of ducted vacuum accessories: hose, wand, floor heads and wall bracket"></div>
      <h1 class="feature-title">Ducted Vacuum</h1>
      <div class="feature-copy">
        <p>Ducted vacuums with Harrowgate Locks and Grilles are the perfect accessory for keeping you home as good as new. With various units ranging from the smaller 2Hp - 2 to 4 outlet unit for the smaller home up to the 4Hp – 5 to 8 outlet unit for larger two story homes and everything in between.</p>
        <p>Don’t get caught up wrestling with and dragging around a corded vacuum. Use a ducted system and all you’ll need to carry is the wand.</p>
      </div>
    </div>
  </section>

  <section class="page page--right">
    <div class="product-photo" role="img" aria-label="Product photo of a grey ducted vacuum power unit"></div>

    <div class="column column--one">
      <div class="section">
        <h2 class="section-heading">An Coastline Vac ducted vacuum improves your health</h2>
        <div class="section-body">
          <p>Every day we breathe in billions of polluting particles around the home. In fact, <strong>the average house collects 18kg of dust a year!</strong> Along with other allergens this can have a major impact on health, especially for asthma and allergy sufferers.</p>
          <p>While portable vacuum cleaners appear to clean a room, they in fact release dust, bacteria and allergens back into the air. Coastline Vac ducted vacuum systems remove all vacuumed dust particles, allergens and noxious odours, creating a healthier living environment</p>
        </div>
      </div>
      <div class="section">
        <h2 class="section-heading">Faster Easier Cleaning</h2>
        <div class="section-body">
          <p>Ducted vacuum systems are versatile enough to be used just about anywhere. Carpets, hard floors, curtains, skirtings, staircases, cars and verandas can all be cleaned with a ducted vacuum system – even the family pet (yes, we have actually tested this – results differ from pet to pet).</p>
          <p>The longer hose and convenient inlet valves of a ducted vacuum help you to reach all parts of your house effortlessly. An Coastline Vac ducted vacuum will speed up and simplify how you clean your home, giving you more time for the important things in life – you and your family.</p>
        </div>
      </div>
    </div>

    <div class="column column--two">
      <div class="section">
        <h2 class="section-heading">More Powerful Suction</h2>
        <div class="section-body">
          <p>An Coastline Vac ducted vacuum system <strong>has</strong> up to five times more power than most conventional portable vacuum cleaners.</p>
          <p>The heavy duty long-life motors used in all Coastline Vac systems ensure hard to shift dust and dirt will be removed from your valuable carpets, soft furnishings and other floor coverings, both protecting them and prolonging their lives. The ducted vacuum system also works well on curtains.</p>
        </div>
      </div>
      <div class="section">
        <h2 class="section-heading">The Cost Effective Cleaning Solution</h2>
        <div class="section-body">
          <p>Did you know that most ducted vacuum systems cost roughly the same as a high quality portable vacuum cleaner? The differences are that ducted vacuum systems last considerably longer (up to four times in fact), are more robust and require less maintenance. It all adds up to a more cost effective investment. Coastline Vac ducted vacuum systems are a semi-permanent feature and an excellent selling point for your home. Why? They not only make cleaning a breeze, they are built to last. That combination will increase the value of your home – well in excess of the original purchase price! As a ducted vacuum system is a semi-permanent structure in your house, it is covered under building insurance.</p>
        </div>
      </div>
    </div>
  </section>
</body>
</html>
```